hotel's Website

Hotels website redesign for reference pictures, logo etc see http://restwellharbour.co.uk/

1. 2-3 Special offers on the main page.
2. Booking calender
3. Location Map
4. Picture gallery.
5. Journeymarks reviews.
6. short description
7. Social Media sharing.
8 Phone number and address.

Industry/Entity Type

Hotel

Requirements
Must have
• 1. 2-3 Special offers on the main page.
2. Booking calender
3. Location Map
4. Picture gallery.
5. Journeymarks reviews.
6. short description
7. Social Media sharing.

```html
<!DOCTYPE html>
<html lang="en">
<head>
<meta charset="utf-8">
<title>Restwell Harbour Victoria</title>
<link rel="stylesheet" href="https://fonts.googleapis.com/css2?family=Noto+Serif:ital,wght@0,400;1,400;1,700&family=Open+Sans:wght@400;600;700&display=swap">
<style>
:root{
  --ink:#1f1f1f;
  --night:#222222;
  --page:#ffffff;
  --amber:#f0a01e;
  --text:#3a3a3a;
  --muted:#9a9a9a;
  --rule:#d6d6d6;
  --link:#39a6d8;
  --brand-blue:#1b4fa8;
}
*{box-sizing:border-box;margin:0;padding:0}
html,body{width:1200px;height:1168px;overflow:hidden}
body{position:relative;background:var(--ink);font-family:"Open Sans",Arial,sans-serif;color:var(--text)}
.backdrop{position:absolute;inset:0;background:linear-gradient(180deg,#2b2b2b 0%,#1c1c1c 45%,#141414 100%)}

/* top bar */
.topbar{position:absolute;left:0;top:0;width:1200px;height:24px;font-size:8.3px;color:#eee}
.topbar .item{position:absolute;top:6px;display:flex;align-items:center;gap:3px}
.book-now{position:absolute;left:848px;top:4px;width:55px;height:15px;background:var(--amber);color:#fff;font-size:9px;font-weight:600;text-align:center;line-height:15px}
.pin-badge{position:absolute;left:316px;top:1px;width:34px;height:34px;border-radius:50%;background:var(--ink);display:flex;align-items:center;justify-content:center;z-index:3}

/* page */
.page{position:absolute;left:234px;top:24px;width:732px;height:861px;background:var(--page)}
.brand{position:absolute;left:64px;top:20px;display:flex;flex-direction:column;align-items:flex-start;gap:4px}
.brand-mark{width:48px;height:52px;background:var(--brand-blue)}
.brand-name{font-size:8px;font-weight:600;color:#333;letter-spacing:.5px;white-space:nowrap}
.nav{position:absolute;top:33px;left:0;width:732px;height:14px;font-family:"Noto Serif",Georgia,serif;font-size:8.3px;letter-spacing:.3px;color:#222;list-style:none}
.nav li{position:absolute;top:0;white-space:nowrap}
.nav .sep{position:absolute;top:-4px;width:1px;height:20px;background:#e0e0e0}
.nav-active{position:absolute;left:176px;top:89px;width:43px;height:3px;background:var(--amber)}

/* hero */
.hero{position:absolute;left:0;top:92px;width:732px;height:328px;background:linear-gradient(180deg,#4a3b6b 0%,#a06a7a 38%,#d98a4a 55%,#3a2a30 72%,#2a1e2e 100%)}
.slide-line{position:absolute;font-family:"Noto Serif",Georgia,serif;font-style:italic;font-weight:700;color:#fff;padding:0 4px;white-space:nowrap}
.slide-line.amber{left:262px;top:84px;height:26px;line-height:26px;background:var(--amber);font-size:12.3px}
.slide-line.dark{left:230px;top:116px;height:28px;line-height:28px;background:rgba(30,30,30,.85);font-size:12.6px}
.hero-arrow{position:absolute;top:140px;width:38px;height:38px;border-radius:50%;background:rgba(255,255,255,.8);display:flex;align-items:center;justify-content:center}

/* booking */
.booking{position:absolute;left:63px;top:383px;width:606px;height:65px;background:var(--night);border-bottom:4px solid var(--amber)}
.field{position:absolute;top:20px;height:21px;background:#fff;font-size:8px;color:#b0b0b0;padding-left:5px;line-height:21px}
.field svg{position:absolute;right:6px;top:6px}
.check-btn{position:absolute;left:498px;top:19px;width:81px;height:21px;background:var(--amber);color:#fff;font-size:8px;font-weight:600;text-align:center;line-height:21px}

/* columns */
.col{position:absolute;top:468px;width:190px;height:240px}
.col-title{font-family:"Noto Serif",Georgia,serif;font-style:italic;font-weight:400;font-size:11px;color:#333;height:22px;border-bottom:1px solid var(--rule);position:relative}
.col-title::after{content:"";position:absolute;left:0;bottom:-3px;width:41px;height:3px;background:var(--amber)}
.photo{position:absolute;width:190px;height:101px;top:43px;left:0}
.col-copy{position:absolute;left:0;top:161px;font-size:8px;line-height:12.5px;color:#333}
.btn-outline{position:absolute;border:1px solid #ccc;font-size:8.5px;color:#444;padding:0 4px;height:21px;line-height:19px;background:#fff}
.offer{position:absolute;left:0;height:40px;width:190px}
.offer-thumb{position:absolute;left:0;top:0;width:45px;height:40px}
.offer-title{position:absolute;left:56px;top:5px;font-size:8.5px;color:#333}
.offer-more{position:absolute;left:56px;top:21px;height:13px;border:1px solid #ccc;font-size:6px;line-height:11px;padding:0 3px;color:#444}

/* gallery */
.gallery-title{position:absolute;left:63px;top:725px;width:606px;height:27px;border-bottom:1px solid var(--rule);font-family:"Noto Serif",Georgia,serif;font-style:italic;font-weight:400;font-size:11px;color:#333}
.gallery-nav{position:absolute;top:727px;width:16px;height:16px;border:1px solid #999;border-radius:50%;display:flex;align-items:center;justify-content:center}
.thumb{position:absolute;top:772px;width:76px;height:57px}

/* footer */
.foot-col{position:absolute;top:920px}
.foot-title{font-size:8px;font-weight:700;letter-spacing:.6px;color:#fff;height:20px;position:relative}
.foot-title::after{content:"";position:absolute;left:0;top:18px;width:41px;height:2px;background:var(--amber)}
.foot-copy{font-size:8px;line-height:11.5px;color:#ddd;margin-top:16px}
.foot-links{list-style:none;font-size:8px;line-height:12px;color:var(--link);margin-top:6px}
.foot-btn{display:inline-block;background:var(--amber);color:#fff;font-size:9px;height:21px;line-height:21px;padding:0 4px;margin-top:12px}
.email-box{width:129px;height:24px;background:#fff;font-size:8.5px;color:#bbb;padding-left:7px;line-height:24px;margin-top:14px}
.review-card{width:120px;height:133px;background:#f4f4f4;margin-top:18px;border:2px solid #6d9a4a;border-top:22px solid #fff}
.socials{display:flex;gap:5px;margin-top:12px}
.socials span{width:24px;height:24px;border-radius:50%;background:#fff}
.foot-rule{position:absolute;left:297px;top:1122px;width:606px;height:1px;background:#444}
.copyright{position:absolute;left:297px;top:1140px;font-size:8px;color:#ddd}
</style>
</head>
<body>
<div class="backdrop" role="img" aria-label="Dark black and white night view of Tower Bridge and the riverside wheel"></div>

<header class="topbar">
  <div class="item" style="left:540px">
    <svg width="8" height="8" viewBox="0 0 10 10"><path d="M2 1l2 2-1 1.5c.6 1.3 1.3 2 2.5 2.5L7 6l2 2-1.2 1.2C4.5 9 1 5.5.8 2.2z" fill="#eee"/></svg>
    <span>+ 44 (0) 20 7946 0321</span>
  </div>
  <div class="item" style="left:648px">
    <svg width="9" height="7" viewBox="0 0 9 7"><rect width="9" height="7" fill="#eee"/><path d="M0 0l4.5 3.5L9 0" stroke="#222" fill="none"/></svg>
    <span>stay@restwellharbour.co.uk</span>
  </div>
  <div class="item" style="left:795px">
    <span>English</span>
    <svg width="6" height="4" viewBox="0 0 6 4"><path d="M0 0h6L3 4z" fill="#eee"/></svg>
  </div>
  <div class="book-now">Book Now</div>
</header>

<div class="pin-badge">
  <svg width="11" height="14" viewBox="0 0 11 14"><path d="M5.5 0A5.5 5.5 0 0 0 0 5.5C0 9 5.5 14 5.5 14S11 9 11 5.5A5.5 5.5 0 0 0 5.5 0z" fill="#fff"/><circle cx="5.5" cy="5.2" r="2" fill="#222"/></svg>
</div>

<main class="page">
  <div class="brand">
    <div class="brand-mark"></div>
    <div class="brand-name">Restwell Harbour</div>
  </div>

  <ul class="nav">
    <li style="left:178px">HOME</li>
    <li class="sep" style="left:213px"></li>
    <li style="left:222px">OUR ROOMS</li>
    <li class="sep" style="left:284px"></li>
    <li style="left:294px">ATTRACTIONS</li>
    <li class="sep" style="left:364px"></li>
    <li style="left:374px">LONDON EVENTS</li>
    <li class="sep" style="left:456px"></li>
    <li style="left:466px">SPECIAL OFFERS</li>
    <li class="sep" style="left:548px"></li>
    <li style="left:559px">PHOTOS</li>
    <li class="sep" style="left:603px"></li>
    <li style="left:614px">DIRECTIONS</li>
    <li class="sep" style="left:677px"></li>
    <li style="left:687px">CONTACT</li>
  </ul>
  <div class="nav-active"></div>

  <section class="hero" role="img" aria-label="Sunset over the Thames with the illuminated riverside wheel and Westminster skyline">
    <div class="slide-line amber">Stay with us for more than 3 nights and enjoy 10% Discount</div>
    <div class="slide-line dark">Discount up to £10 when you stay with us for the night of Sunday!</div>
    <div class="hero-arrow" style="left:28px"><svg width="8" height="14" viewBox="0 0 8 14"><path d="M7 1L1 7l6 6" stroke="#555" fill="none"/></svg></div>
    <div class="hero-arrow" style="left:665px"><svg width="8" height="14" viewBox="0 0 8 14"><path d="M1 1l6 6-6 6" stroke="#555" fill="none"/></svg></div>
  </section>

  <form class="booking">
    <div class="field" style="left:19px;width:119px">Check In
      <svg width="9" height="9" viewBox="0 0 9 9"><rect x=".5" y="1.5" width="8" height="7" fill="none" stroke="#777"/><path d="M.5 3.5h8M3 3.5v5M6 3.5v5M.5 6h8" stroke="#777"/></svg></div>
    <div class="field" style="left:144px;width:119px">Check Out
      <svg width="9" height="9" viewBox="0 0 9 9"><rect x=".5" y="1.5" width="8" height="7" fill="none" stroke="#777"/><path d="M.5 3.5h8M3 3.5v5M6 3.5v5M.5 6h8" stroke="#777"/></svg></div>
    <div class="field" style="left:269px;width:107px">Adults
      <svg width="9" height="6" viewBox="0 0 9 6" style="top:8px"><path d="M0 0h9L4.5 5z" fill="#333"/></svg></div>
    <div class="field" style="left:383px;width:107px">Children
      <svg width="9" height="6" viewBox="0 0 9 6" style="top:8px"><path d="M0 0h9L4.5 5z" fill="#333"/></svg></div>
    <div class="check-btn">Check Availability</div>
  </form>

  <section class="col" style="left:63px">
    <h2 class="col-title">About Restwell Harbour</h2>
    <div class="photo" role="img" aria-label="White Georgian townhouse hotel frontage with black railings" style="background:linear-gradient(180deg,#b49a7a 0%,#e8e4da 45%,#f0eee8 70%,#3a3a3a 100%)"></div>
    <p class="col-copy">This tastefully appointed four storey building<br>is comprised of three attractive Georgian<br>style townhouses...</p>
    <div class="btn-outline" style="top:211px;left:0">Read More</div>
  </section>

  <section class="col" style="left:271px">
    <h2 class="col-title">Special Offers</h2>
    <div class="offer" style="top:44px">
      <div class="offer-thumb" role="img" aria-label="Spa treatment" style="background:linear-gradient(135deg,#e6c7a8,#f3e6d8)"></div>
      <div class="offer-title">25% off on Spa Treatments</div>
      <div class="offer-more">Read More</div>
    </div>
    <div class="offer" style="top:90px">
      <div class="offer-thumb" role="img" aria-label="Calendar page" style="background:linear-gradient(135deg,#ddd,#f5f5f5)"></div>
      <div class="offer-title">Sunday Special</div>
      <div class="offer-more">Read More</div>
    </div>
    <div class="offer" style="top:137px">
      <div class="offer-thumb" role="img" aria-label="Shoppers with bags in the city" style="background:linear-gradient(135deg,#8a9aa8,#c9a890)"></div>
      <div class="offer-title">Shopping in London</div>
      <div class="offer-more">Read More</div>
    </div>
    <div class="offer" style="top:184px">
      <div class="offer-thumb" role="img" aria-label="Silver hire car" style="background:linear-gradient(180deg,#cfd6d8,#4a4a4a)"></div>
      <div class="offer-title">Low Cost Car Hire</div>
      <div class="offer-more">Read More</div>
    </div>
  </section>

  <section class="col" style="left:479px">
    <h2 class="col-title">London Events</h2>
    <div class="photo" role="img" aria-label="Halloween scene with pumpkins and candles" style="background:linear-gradient(180deg,#3a2e22 0%,#5a3a22 55%,#b8561c 100%)"></div>
    <p class="col-copy">Halloween at the Thameside Vaults<br>(26th Oct 13 to 3rd Nov 13)</p>
    <div class="btn-outline" style="top:198px;left:0">Read More</div>
  </section>

  <h2 class="gallery-title">Picture Gallery</h2>
  <div class="gallery-nav" style="left:630px"><svg width="5" height="7" viewBox="0 0 5 7"><path d="M4 .5L1 3.5l3 3" stroke="#222" fill="none"/></svg></div>
  <div class="gallery-nav" style="left:651px"><svg width="5" height="7" viewBox="0 0 5 7"><path d="M1 .5l3 3-3 3" stroke="#222" fill="none"/></svg></div>

  <div class="thumb" style="left:63px;background:linear-gradient(180deg,#8a8378,#d9c640 60%,#3a3a3a)" role="img" aria-label="Lit reception desk"></div>
  <div class="thumb" style="left:151px;background:linear-gradient(180deg,#e8e2d8,#c8a898 60%,#8a3a2a)" role="img" aria-label="Double bedroom"></div>
  <div class="thumb" style="left:240px;background:linear-gradient(135deg,#5a6a8a,#e2b030 55%,#c8463a)" role="img" aria-label="Colourful lounge"></div>
  <div class="thumb" style="left:328px;background:linear-gradient(180deg,#eee8dc,#a87a4a)" role="img" aria-label="Kitchenette with table"></div>
  <div class="thumb" style="left:417px;background:linear-gradient(180deg,#e8d890,#8a2a22)" role="img" aria-label="Studio room with red carpet"></div>
  <div class="thumb" style="left:505px;background:linear-gradient(180deg,#e8dcc8,#b87a4a)" role="img" aria-label="Dining area"></div>
  <div class="thumb" style="left:593px;background:linear-gradient(135deg,#d8d4cc,#e0cc30 55%,#c83a6a)" role="img" aria-label="Sofa with bright cushions"></div>
</main>

<footer>
  <div class="foot-col" style="left:297px;width:140px">
    <h3 class="foot-title">PARTNER'S HOTEL</h3>
    <p class="foot-copy">This hotel is owned and operated by the Northgate Hotel Group, please take a look of some of our other hotels below:</p>
    <ul class="foot-links">
      <li>Larkspur Inn London - Canal Side</li>
      <li>Larkspur Express - West Court</li>
      <li>Meridian House Hotel</li>
      <li>Brightstay Victoria</li>
    </ul>
    <span class="foot-btn">Read More</span>
  </div>
  <div class="foot-col" style="left:452px;width:135px">
    <h3 class="foot-title">NEWSLETTER</h3>
    <p class="foot-copy" style="font-weight:600;color:#fff">Sign up for our newsletter for latest news</p>
    <div class="email-box">Email</div>
    <span class="foot-btn">Subscribe</span>
  </div>
  <div class="foot-col" style="left:607px">
    <h3 class="foot-title">JOURNEYMARKS</h3>
    <div class="review-card" role="img" aria-label="Journeymarks reviews panel"></div>
  </div>
  <div class="foot-col" style="left:761px">
    <h3 class="foot-title">SOCIAL MEDIA</h3>
    <div class="socials" aria-label="Social media links"><span></span><span></span><span></span><span></span><span></span></div>
  </div>
  <div class="foot-rule"></div>
  <p class="copyright">© Copyright 2013. Restwell Harbour Victoria. All Rights Reserved</p>
</footer>
</body>
</html>
```